Corvane Holdings , new business card design

investment firm with corporate clients . need double sided business card , vertical and horizontal options ,logo must be clear. prefer pantone colors only and sharp design. website also www.corvane.ae

Khalid Bin Tarrafi
Managing Director
Tel. +971 4 387 2940
Mobile +971 50 518 2403
khalid@corvane.ae
Q-Span Plaza, officw 18-B07, Warqa Gardens, Dubai

Contact Information for Business Card

Khalid Bin Tarrafi
Managing Director

Font styles to use
Serif

Colors

Designer to choose colors to be used in the design.

```html
<!DOCTYPE html>
<html lang="en">
<head>
<meta charset="utf-8">
<title>Corvane Holdings – Business Card</title>
<link rel="stylesheet" href="https://fonts.googleapis.com/css2?family=Questrial&family=Montserrat:wght@700&display=swap">
<style>
  :root {
    --ink: #0b0c12;
    --paper: #ffffff;
    --steel-blue: #44729d;
    --text-dark: #2a2a2a;
    --backdrop: #ecebe8;
  }
  * { box-sizing: border-box; margin: 0; padding: 0; }
  html, body { width: 1200px; height: 900px; overflow: hidden; }
  body {
    background: var(--backdrop);
    position: relative;
    font-family: "Questrial", "Century Gothic", sans-serif;
  }
  .card {
    position: absolute;
    width: 620px;
    height: 354px;
    box-shadow: 0 6px 18px rgba(0,0,0,0.18);
    overflow: hidden;
  }
  /* Front side */
  .card--front {
    left: 80px; top: 100px;
    background: var(--ink);
    color: var(--paper);
    display: flex; flex-direction: column; align-items: center; justify-content: center;
  }
  .brand-name {
    text-align: center;
    font-family: "Questrial", "Century Gothic", sans-serif;
    font-weight: 400;
    line-height: 1.1;
    text-transform: uppercase;
    color: var(--paper);
  }
  .brand-name__main { display: block; font-size: 50px; letter-spacing: 16px; padding-left: 16px; }
  .brand-name__sub { display: block; font-size: 15px; letter-spacing: 15px; padding-left: 15px; margin-top: 8px; }
  .card--front .website { margin-top: 38px; font-size: 15px; letter-spacing: 0.5px; }

  /* Back side */
  .card--back {
    left: 500px; top: 446px;
    background: var(--paper);
    color: var(--text-dark);
  }
  .card__wave { position: absolute; inset: 0; width: 100%; height: 100%; }
  .holder {
    position: absolute; left: 46px; top: 40px;
  }
  .holder__name {
    font-family: "Montserrat", sans-serif;
    font-weight: 700;
    font-size: 21px;
    color: var(--steel-blue);
    text-transform: uppercase;
    letter-spacing: 0.3px;
  }
  .holder__title { font-size: 16px; margin-top: 2px; padding-left: 8px; }
  .card--back .brand-name {
    position: absolute; right: 30px; top: 72px;
    color: var(--ink);
  }
  .card--back .brand-name__main { font-size: 36px; letter-spacing: 12px; padding-left: 12px; }
  .card--back .brand-name__sub { font-size: 11px; letter-spacing: 11px; padding-left: 11px; margin-top: 5px; }
  .contact {
    position: absolute; left: 70px; top: 152px;
    list-style: none; font-size: 16px; line-height: 21px;
  }
  .contact li { display: flex; align-items: center; gap: 8px; }
  .contact svg { width: 14px; height: 14px; fill: var(--steel-blue); flex: none; }
  .address {
    position: absolute; left: 92px; top: 224px;
    font-size: 16px; line-height: 21px; font-style: normal;
  }
  .card--back .website {
    position: absolute; right: 28px; top: 214px;
    color: var(--paper); font-size: 14px;
  }
</style>
</head>
<body>

  <section class="card card--front" aria-label="Card front">
    <div class="brand-name">
      <span class="brand-name__main">Corvane</span>
      <span class="brand-name__sub">Holdings</span>
    </div>
    <p class="website">www.corvane.ae</p>
  </section>

  <section class="card card--back" aria-label="Card back">
    <svg class="card__wave" viewBox="0 0 620 354" preserveAspectRatio="none" aria-hidden="true">
      <path fill="var(--ink)" d="M0,300 C170,330 390,300 620,150 L620,354 L0,354 Z"/>
      <path fill="var(--steel-blue)" d="M0,282 C170,316 390,282 540,182 C400,290 170,318 0,294 Z"/>
    </svg>

    <div class="holder">
      <h1 class="holder__name">Khalid Bin Tarrafi</h1>
      <p class="holder__title">Managing Director</p>
    </div>

    <div class="brand-name">
      <span class="brand-name__main">Corvane</span>
      <span class="brand-name__sub">Holdings</span>
    </div>

    <ul class="contact">
      <li>
        <svg viewBox="0 0 16 16" aria-hidden="true"><path d="M2 5c0-2 2-3 6-3s6 1 6 3v1h-3V5H5v1H2zM4 7h8l2 6H2z"/></svg>
        +971 4 387 2940
      </li>
      <li>
        <svg viewBox="0 0 16 16" aria-hidden="true"><path d="M5 0h6a1 1 0 0 1 1 1v14a1 1 0 0 1-1 1H5a1 1 0 0 1-1-1V1a1 1 0 0 1 1-1zm0 2v10h6V2zm3 11a1 1 0 1 0 0 2 1 1 0 0 0 0-2z"/></svg>
        +971 50 518 2403
      </li>
      <li>
        <svg viewBox="0 0 16 16" aria-hidden="true"><path d="M1 3h14v10H1zm1.5 1.2L8 8.5l5.5-4.3z"/></svg>
        khalid@corvane.ae
      </li>
    </ul>

    <address class="address">
      Q-Span Plaza, officw 18-B07<br>
      Warqa Gardens, Dubai
    </address>

    <p class="website">www.corvane.ae</p>
  </section>

</body>
</html>
```